Clean business card with logo provided

I want a card that will stand out among the masses. I need the color and image to show professionalism and yet have a family appeal showing that I only deal with win/win scenarios. The back of the card will be used to take notes about the individual so I can use that in my database entry. I like modern design but need professionalism in it also. It needs to fit my "clean, safe, and affordable housing" motto. I need to be able to write on the file and update the card details for my employees.

Target Market(s)

Investors looking to make investment income through real estate

Industry/Entity Type

Real Estate

Contact Information for Business Card

Brent Kovalich
blank address, city, st, zip code
480-555-3174
brentkovalich@ridgeworthrentals.example
www.ridgeworthrentals.example

Font styles to use
Sans Serif

Requirements
Must have
• I would like the back of the card to have lines for info. example
• Met/Visited: Date:
• Interets:
Nice to have
• I want the cards color to match the logo background color. Font with details to be san serif and black. I want the card rectangular with square corners. Standard business card size. I would like to see cards designed with both images to see which i prefer more.

```html
<!DOCTYPE html>
<html lang="en">
<head>
<meta charset="utf-8">
<title>Ridgeworth Rentals LLC – Business Card</title>
<link rel="stylesheet" href="https://fonts.googleapis.com/css2?family=Lato:wght@400;700&display=swap">
<style>
  :root {
    --teal: #24c3d6;
    --ink: #121212;
    --paper: #f5f5f4;
    --text: #1c1c1c;
    --backdrop: #2e2e30;
    --dots: #444;
  }
  * { margin: 0; padding: 0; box-sizing: border-box; }
  html, body {
    width: 1200px; height: 900px; overflow: hidden;
    background: var(--backdrop);
    font-family: "Lato", sans-serif;
  }
  .canvas { position: relative; width: 1200px; height: 900px; }

  .card {
    position: absolute;
    width: 600px; height: 343px;
    background: var(--paper);
    overflow: hidden;
  }

  /* ---------- Notes side ---------- */
  .card-notes { left: 70px; top: 60px; }
  .card-notes .band-top { position: absolute; left: 0; top: 0; width: 100%; height: 22px; background: var(--teal); }
  .card-notes .band-bottom { position: absolute; left: 0; bottom: 0; width: 100%; height: 42px; background: var(--teal); }
  .card-notes .brand-box {
    position: absolute; right: 40px; top: 0;
    width: 250px; height: 96px;
    background: var(--teal);
    display: flex; flex-direction: column; justify-content: center; align-items: center;
    gap: 6px; text-align: center;
  }
  .card-notes .brand-name { color: var(--ink); font-size: 17px; font-weight: 700; letter-spacing: 1px; line-height: 1.2; }
  .card-notes .brand-tagline { color: var(--ink); font-size: 9px; letter-spacing: .3px; white-space: nowrap; }

  .note-field { position: absolute; display: flex; align-items: flex-end; color: var(--teal); font-size: 17px; white-space: nowrap; }
  .note-field .line { flex: 1; border-bottom: 2px dotted var(--dots); margin-left: 8px; height: 1px; margin-bottom: 5px; }
  .note-line { position: absolute; border-bottom: 2px dotted var(--dots); }

  /* ---------- Contact side ---------- */
  .card-contact { left: 520px; top: 495px; }
  .card-contact .band-top { position: absolute; left: 0; top: 0; width: 100%; height: 30px; background: var(--ink); }
  .card-contact .band-bottom { position: absolute; left: 0; bottom: 0; width: 100%; height: 30px; background: var(--ink); }
  .card-contact .brand-box {
    position: absolute; left: 36px; top: 0;
    width: 270px; height: 150px;
    background: var(--ink);
    display: flex; flex-direction: column; justify-content: center; align-items: center;
    gap: 10px;
  }
  .card-contact .brand-name { color: var(--teal); font-size: 20px; font-weight: 700; letter-spacing: 1.2px; text-align: center; line-height: 1.3; }
  .card-contact .brand-tagline { color: var(--teal); font-size: 10px; letter-spacing: .3px; white-space: nowrap; }

  .holder-name {
    position: absolute; left: 40px; bottom: 52px;
    font-size: 26px; font-weight: 700; color: var(--ink); letter-spacing: .5px;
    white-space: nowrap;
  }

  .contact-list {
    position: absolute; left: 296px; top: 168px;
    border-left: 1.5px solid var(--teal);
    padding-left: 12px;
    list-style: none;
    font-size: 12px; color: var(--text);
  }
  .contact-list li { display: flex; align-items: center; gap: 8px; height: 27px; white-space: nowrap; }
  .contact-list li.email { border-bottom: 1.5px solid var(--teal); }
  .contact-list svg { width: 12px; height: 12px; fill: var(--ink); flex: none; }
</style>
</head>
<body>
<main class="canvas">

  <section class="card card-notes" aria-label="Card back, notes side">
    <div class="band-top"></div>
    <div class="brand-box">
      <span class="brand-name">RIDGEWORTH<br>RENTALS LLC</span>
      <span class="brand-tagline">Providing clean, safe, and affordable housing</span>
    </div>
    <div class="note-field" style="left:48px; top:112px; width:512px;">Meet/Visited :<span class="line"></span></div>
    <div class="note-line" style="left:48px; top:168px; width:512px;"></div>
    <div class="note-field" style="left:48px; top:190px; width:300px;">Date:<span class="line"></span></div>
    <div class="note-field" style="left:364px; top:190px; width:196px;">Time:<span class="line"></span></div>
    <div class="note-field" style="left:48px; top:230px; width:512px;">INTERETS :<span class="line"></span></div>
    <div class="note-line" style="left:48px; top:284px; width:512px;"></div>
    <div class="band-bottom"></div>
  </section>

  <section class="card card-contact" aria-label="Card front, contact side">
    <div class="band-top"></div>
    <div class="brand-box">
      <span class="brand-name">RIDGEWORTH<br>RENTALS LLC</span>
      <span class="brand-tagline">Providing clean, safe, and affordable housing</span>
    </div>

    <ul class="contact-list">
      <li>
        <svg viewBox="0 0 24 24" aria-hidden="true"><path d="M6.6 10.8a15 15 0 0 0 6.6 6.6l2.2-2.2a1 1 0 0 1 1-.25 11.4 11.4 0 0 0 3.6.57 1 1 0 0 1 1 1V20a1 1 0 0 1-1 1A17 17 0 0 1 3 4a1 1 0 0 1 1-1h3.5a1 1 0 0 1 1 1c0 1.25.2 2.45.57 3.6a1 1 0 0 1-.25 1z"/></svg>
        480-555-3174
      </li>
      <li>
        <svg viewBox="0 0 24 24" aria-hidden="true"><circle cx="12" cy="12" r="10" fill="none" stroke="#121212" stroke-width="2"/><path d="M2 12h20M12 2c3 3 3 17 0 20M12 2c-3 3-3 17 0 20" fill="none" stroke="#121212" stroke-width="1.6"/></svg>
        www.ridgeworthrentals.example
      </li>
      <li class="email">
        <svg viewBox="0 0 24 24" aria-hidden="true"><path d="M2 5h20v14H2z"/><path d="M2 5l10 8 10-8" fill="none" stroke="#f5f5f4" stroke-width="1.6"/></svg>
        brentkovalich@ridgeworthrentals.example
      </li>
      <li>
        <svg viewBox="0 0 24 24" aria-hidden="true"><path d="M12 2a7 7 0 0 0-7 7c0 5 7 13 7 13s7-8 7-13a7 7 0 0 0-7-7zm0 9.5A2.5 2.5 0 1 1 12 6.5a2.5 2.5 0 0 1 0 5z"/></svg>
        blank address, city, st, zip code
      </li>
    </ul>

    <h1 class="holder-name">BRENT KOVALICH</h1>
    <div class="band-bottom"></div>
  </section>

</main>
</body>
</html>
```